Business Card for premium dental clinic

We are a premium dental clinic based in Brasov, Romania with more than 15 year on the market, providing quality dental treatment made by a team of more specialized dentists, working with modern equipment as a solution to beautiful and healthy teeth.

Our current logo for the clinic use 2 square with colors black and gold - dr Ternisu - studio, using family fonts Bodoni, Myriad Pro and Segoe Print.
Depending on the printing we used some gold CMYK background or gold foil picture background or a gold gradient.
We want a business card:
- eye catching business card
- distinguished business card
- premium design
- to keep the color scheme of black and gold
- to attract the customers to spent time reading the information
- modern concept

```html
<!DOCTYPE html>
<html lang="en">
<head>
<meta charset="utf-8">
<title>dr Ternisu – Business Card</title>
<link href="https://fonts.googleapis.com/css2?family=Jost:wght@400;500&display=swap" rel="stylesheet">
<style>
  :root {
    --ink: #231f20;
    --gold: #f2bf1e;
    --gold-light: #f6c84a;
    --gold-deep: #d9951a;
    --paper: #ffffff;
    --font: "Jost", "Futura", sans-serif;
  }
  html, body {
    margin: 0; padding: 0;
    width: 902px; height: 1200px;
    overflow: hidden;
    background: var(--paper);
    font-family: var(--font);
  }
  .card {
    position: absolute;
    width: 744px; height: 433px;
    border-radius: 20px;
    overflow: hidden;
    background: var(--ink);
    box-shadow: 3px 5px 8px rgba(0,0,0,.25);
  }
  .card--front { left: 75px; top: 132px; }
  .card--back  { left: 77px; top: 629px; }
  .card__art { position: absolute; inset: 0; }

  .identity { position: absolute; left: 65px; top: 70px; color: var(--gold); }
  .identity__name { margin: 0; font-size: 28px; font-weight: 400; line-height: 1; letter-spacing: .3px; }
  .identity__role { margin: 4px 0 0; font-size: 17px; line-height: 1.1; }

  .address { position: absolute; left: 65px; top: 214px; margin: 0;
    color: var(--gold); font-size: 17px; line-height: 22px; font-style: normal; }

  .contacts { position: absolute; left: 65px; top: 302px; margin: 0; padding: 0;
    list-style: none; color: var(--gold); font-size: 17px; line-height: 22px; }
  .contacts li { display: flex; align-items: center; }
  .contacts svg { width: 12px; height: 12px; margin-right: 11px; fill: var(--gold); }

  .brand { position: absolute; display: flex; align-items: center; }
  .brand__label { background: var(--paper); color: var(--ink); font-weight: 400;
    white-space: nowrap; display: flex; align-items: center; justify-content: center; }
  .brand__square { background: var(--ink); }

  .card--front .brand { left: 434px; top: 168px; }
  .card--front .brand__label { width: 107px; height: 40px; font-size: 19px; }
  .card--front .brand__square { width: 130px; height: 122px; margin-left: 2px; }

  .card--back .brand { left: 100px; top: 129px; }
  .card--back .brand__label { width: 170px; height: 64px; font-size: 30px; }
  .card--back .brand__square { width: 201px; height: 189px; margin-left: 2px; }
</style>
</head>
<body>

<section class="card card--front">
  <svg class="card__art" viewBox="0 0 744 433" aria-hidden="false">
    <defs>
      <radialGradient id="foil-front" cx="60%" cy="45%" r="70%">
        <stop offset="0" stop-color="#f6c84a"/>
        <stop offset=".6" stop-color="#f0b52a"/>
        <stop offset="1" stop-color="#d9951a"/>
      </radialGradient>
    </defs>
    <circle cx="688" cy="217" r="334" fill="#ffffff"/>
    <circle cx="688" cy="217" r="322" fill="url(#foil-front)" role="img" aria-label="Textured gold foil background"/>
  </svg>

  <header class="identity">
    <h1 class="identity__name">DR. TERNISU</h1>
    <p class="identity__role">Dental specialist</p>
  </header>

  <address class="address">7th floor, Lindor Street no<br>48 Tower Centru</address>

  <ul class="contacts">
    <li><svg viewBox="0 0 12 12"><path d="M2.4 0.6l2 2.2-1 1.4c.8 1.6 2 2.8 3.6 3.6l1.4-1 2.2 2-1.2 2.2C5.2 10.8 1.2 6.8 0.2 1.8z"/></svg>0268401953</li>
    <li><svg viewBox="0 0 12 12"><path d="M0 2.5h12v7H0z M0 2.5l6 4 6-4" stroke="#231f20" stroke-width=".8"/></svg>andrei.moldo@ternisustudio.ro</li>
    <li><svg viewBox="0 0 12 12"><circle cx="6" cy="6" r="5.5"/><path d="M3 3.5c1 .3 1.6 1 1.3 2s.8 1.6 1.5 1.4M7.5 2.5c-.5 1 .2 1.8 1.4 1.6M6.5 9.5c.3-1 1.3-1.5 2.5-1.2" stroke="#231f20" stroke-width=".9" fill="none"/></svg>www.ternisustudio.ro</li>
  </ul>

  <div class="brand">
    <span class="brand__label">dr Ternisu</span>
    <span class="brand__square"></span>
  </div>
</section>

<section class="card card--back">
  <svg class="card__art" viewBox="0 0 744 433">
    <defs>
      <radialGradient id="foil-back" cx="40%" cy="45%" r="70%">
        <stop offset="0" stop-color="#f6c84a"/>
        <stop offset=".6" stop-color="#f0b52a"/>
        <stop offset="1" stop-color="#d9951a"/>
      </radialGradient>
    </defs>
    <circle cx="226" cy="217" r="371" fill="#ffffff"/>
    <circle cx="226" cy="217" r="359" fill="url(#foil-back)" role="img" aria-label="Textured gold foil background"/>
  </svg>

  <div class="brand">
    <span class="brand__label">dr Ternisu</span>
    <span class="brand__square"></span>
  </div>
</section>

</body>
</html>
```